Logo, Web and Mobile Designs for enterprise social media platform

All the details are in the attached document, please start reading the scope document first which explains what is this project about and the details about the needed deliverables, after that please read the UI_Requirements document which will detail what is expected regarding the coded web version since this is a coded contest, it is very important that you meet the UI requirements or suggest something else but we will need to agree first before working on the coded version

Good Luck

Target Market(s)

Enterprise Social Media

Industry/Entity Type

Media

Coding

Coded - Design and coding required

Number of Pages Required

5+ page

Font styles to use
Sans Serif

Requirements
Must have
• All the must haves are listed in the scope document so please check before you start

```html
<!DOCTYPE html>
<html lang="en">
<head>
<meta charset="utf-8">
<title>Teamora — Company Wall</title>
<link rel="stylesheet" href="https://fonts.googleapis.com/css2?family=Open+Sans:ital,wght@0,400;0,600;0,700;1,600&display=swap">
<style>
:root{
  --navy:#2b4666;
  --navy-deep:#253d5a;
  --ink:#1f3a5f;
  --text:#555b63;
  --muted:#8a9099;
  --band:#e4eefa;
  --line:#e3e6ea;
  --online:#1fb82c;
  --offline:#9a9a9a;
  --alert:#e0262b;
  --friendnet:#3b5a9a;
  --chirpline:#2b9fe0;
  --rss:#f08a24;
  --circle:#d6392b;
  --page:#ffffff;
}
*{box-sizing:border-box;margin:0;padding:0}
html,body{width:1200px;height:2233px;overflow:hidden}
body{position:relative;background:var(--page);font-family:"Open Sans",Arial,sans-serif;color:var(--text)}
a{color:inherit;text-decoration:none}

/* header */
.site-header{position:absolute;left:0;top:0;width:1200px;height:98px;background:var(--navy)}
.brand{position:absolute;left:97px;top:30px;color:#fff;font-size:26px;font-weight:400;letter-spacing:1.5px}
.search{position:absolute;left:334px;top:24px;width:330px;height:43px;background:#fff;border-radius:4px;display:flex;align-items:center}
.search span{flex:1;padding-left:20px;font-size:12px;color:#777}
.search .search-btn{width:56px;height:43px;border-left:1px solid #ddd;display:flex;align-items:center;justify-content:center}
.header-icon{position:absolute;top:30px}
.badge{position:absolute;top:-8px;right:-10px;width:17px;height:17px;border-radius:50%;background:var(--alert);color:#fff;font-size:9px;line-height:17px;text-align:center}
.main-nav{position:absolute;top:38px;left:890px;display:flex;gap:26px;color:#fff;font-size:12px;font-weight:600}

/* cover */
.cover{position:absolute;left:100px;top:122px;width:1000px;height:459px;border:3px solid #e6e6e6;background:linear-gradient(135deg,#b57b45 0%,#9a6435 40%,#c68a52 75%,#8a5a30 100%)}
.profile-photo{position:absolute;left:152px;top:412px;width:218px;height:218px;border-radius:50%;border:4px solid #fff;background:radial-gradient(circle at 50% 40%,#d9cfc6,#8e8a86)}
.profile-tabs{position:absolute;top:594px;left:369px;display:flex;align-items:center;font-size:13px;color:#888}
.profile-tabs .tab{width:102px;text-align:center}
.profile-tabs .tab.active{width:70px;height:34px;line-height:34px;background:linear-gradient(#f4f4f4,#d6d6d6);border:1px solid #c8c8c8;border-radius:4px;color:var(--ink);font-weight:600;margin-right:16px}

/* columns */
.panel{position:absolute;border:1px solid var(--line);background:#fff}
.band{height:41px;background:var(--band);border-top:3px solid var(--navy);text-align:center;color:var(--ink);font-size:17px;line-height:38px}
.load-more{display:block;text-align:center;color:var(--ink);font-size:12px;font-style:italic;font-weight:600;text-decoration:underline}
.thumb{border-radius:2px}

.welcome{left:97px;top:668px;width:254px;height:78px;padding:14px 18px;color:var(--ink);font-size:16px;line-height:28px;background:#f8f9fb}
.welcome svg{position:absolute;right:12px;bottom:12px}

.left-col{left:97px;top:779px;width:254px;height:1228px;border-top:none}
.biz-item{display:flex;gap:16px;padding:0 12px;margin-top:29px}
.biz-item .thumb{width:92px;height:82px;flex:none}
.item-text{font-size:12.5px;line-height:20px;color:var(--muted)}
.item-text strong{display:block;color:var(--ink);font-weight:400}
.item-links{margin-top:2px;color:var(--ink)}
.item-links a:first-child{text-decoration:underline;margin-right:24px}
.divider{height:1px;background:var(--line);margin:16px 40px 0}
.events-band{margin-top:36px}
.event-item{display:flex;gap:24px;padding:0 0 0 22px;margin-top:30px}
.event-item .thumb{width:71px;height:62px;flex:none}
.event-item strong{display:block;color:var(--ink);font-size:12.5px;font-weight:600;letter-spacing:.3px}
.event-item em{display:block;color:var(--ink);font-size:11px;font-weight:600;font-style:italic}
.event-item .item-links{font-size:13px;margin-top:4px}

/* wall */
.wall-head{position:absolute;left:384px;top:667px;width:431px}
.wall-head h2{font-size:16px;font-weight:600;color:var(--ink);display:flex;align-items:center;gap:14px}
.wall-head h2 span{font-size:12px;color:var(--muted);font-weight:400;display:flex;gap:6px;align-items:center}
.status-box{margin-top:14px;height:29px;border:1px solid #cfd4da;padding-left:10px;line-height:27px;font-size:11px;color:#999}
.wall-head p{margin-top:15px;font-size:13px;color:var(--ink)}

.post{left:384px;width:431px;height:405px;padding:0}
.post .share{position:absolute;right:10px;top:6px;font-size:12px;color:#444;display:flex;gap:5px;align-items:center}
.post .avatar{position:absolute;left:12px;top:24px;width:67px;height:69px;background:linear-gradient(#e2d8cf,#8d8680);border:1px solid #ddd}
.post .meta{position:absolute;left:97px;top:26px}
.post h3{font-size:14px;font-weight:600;color:var(--ink)}
.post .src{font-size:12px;color:var(--muted);margin-top:4px}
.post .date{font-size:12.5px;color:var(--ink);margin-top:4px;display:flex;align-items:center;gap:8px}
.post .body{position:absolute;left:10px;right:10px;top:112px;font-size:13px;line-height:21.5px;color:#4b4f55}
.post .video{position:absolute;left:10px;top:193px;width:410px;height:152px}
.post .video svg{position:absolute;left:182px;top:53px}
.post .actions{position:absolute;left:24px;top:359px;display:flex;gap:38px;font-size:13px;color:var(--muted)}
.post .actions span{display:flex;align-items:center;gap:7px}

/* right column */
.right-col{left:847px;top:668px;width:253px;height:1339px;border-top:none}
.feed-item{display:flex;align-items:center;gap:20px;padding-left:57px;font-size:17px;font-weight:600;height:44px;margin-top:22px}
.feed-item:first-of-type{margin-top:30px}
.feed-item i{width:44px;height:44px;display:block;border-radius:3px}
.friends-band{margin-top:42px;position:relative}
.friends-band b{position:absolute;left:154px;top:4px;width:14px;height:14px;border-radius:50%;background:var(--navy);color:#fff;font-size:8px;line-height:14px;font-weight:400}
.friend-list{list-style:none;padding:10px 0 0 40px}
.friend-list li{height:35px;line-height:35px;font-size:12.5px;color:var(--ink);display:flex;align-items:center;gap:18px}
.friend-list li::before{content:"";width:12px;height:12px;border-radius:50%;background:var(--offline)}
.friend-list li.on::before{background:var(--online)}
.pc-band{margin-top:42px}
.pc-item{display:flex;gap:10px;padding-left:10px;margin-top:20px}
.pc-item .thumb{width:62px;height:62px;flex:none}
.pc-item strong{display:block;color:var(--ink);font-size:14.5px;font-weight:600}
.pc-item span{display:block;color:var(--muted);font-size:12px;line-height:18px}
.pc-item small{font-size:12px;color:var(--ink)}
.pc-item small em{font-style:normal;color:var(--muted);font-size:10px;margin-left:6px}

.loader{position:absolute;left:580px;top:2075px;text-align:center;font-size:7px;color:#333}
.site-footer{position:absolute;left:0;top:2159px;width:1200px;height:74px;background:var(--navy-deep);color:#fff;text-align:center;line-height:74px;font-size:14px}
</style>
</head>
<body>

<header class="site-header">
  <div class="brand">TEAMORA</div>
  <div class="search"><span>search here ...</span><div class="search-btn">
    <svg width="22" height="22" viewBox="0 0 22 22"><circle cx="9" cy="9" r="6" fill="none" stroke="#2b4666" stroke-width="2.4"/><line x1="13.5" y1="13.5" x2="20" y2="20" stroke="#2b4666" stroke-width="3"/></svg></div></div>
  <div class="header-icon" style="left:700px"><svg width="36" height="28" viewBox="0 0 36 28"><circle cx="13" cy="8" r="6" fill="#fff"/><path d="M2 26c0-8 5-11 11-11s11 3 11 11z" fill="#fff"/><circle cx="24" cy="8" r="5" fill="none" stroke="#fff" stroke-width="1.6"/><path d="M24 15c6 0 10 3 10 10" fill="none" stroke="#fff" stroke-width="1.6"/></svg></div>
  <div class="header-icon" style="left:760px"><svg width="28" height="26" viewBox="0 0 28 26"><path d="M2 4h18v12H9l-5 5v-5H2z" fill="#fff"/><path d="M22 8h4v11h-2v4l-4-4h-8v-2" fill="none" stroke="#fff" stroke-width="1.6"/></svg><span class="badge">12</span></div>
  <div class="header-icon" style="left:810px"><svg width="26" height="26" viewBox="0 0 26 26"><circle cx="13" cy="13" r="11" fill="#fff"/><path d="M6 8c3 1 4 4 3 7s2 5 4 5M15 4c0 3 3 4 6 4M16 14c2 0 4 2 3 5" fill="none" stroke="#2b4666" stroke-width="1.6"/></svg><span class="badge">12</span></div>
  <nav class="main-nav"><a>HOME</a><a>ACCOUNT ▾</a><a>SIGN IN</a></nav>
</header>

<div class="cover" role="img" aria-label="Cover photo: team around a wooden table with social media icons"></div>
<div class="profile-photo" role="img" aria-label="Profile photo of the company representative"></div>

<nav class="profile-tabs"><span class="tab active">wall</span><span class="tab">info</span><span class="tab">photos</span><span class="tab">stories</span><span class="tab">vidstream</span></nav>

<div class="panel welcome">Welcome to official page of teamora
  <svg width="16" height="14" viewBox="0 0 16 14"><path d="M1 6h3v8H1zM5 6l4-6c2 0 2 2 1 4h5l-1 10H5z" fill="#2b4666"/></svg></div>

<aside class="panel left-col">
  <div class="band">Business Oppurtunities</div>
  <div class="biz-item"><div class="thumb" role="img" aria-label="Conference audience photo" style="background:linear-gradient(135deg,#3a3f4a,#7b7f88)"></div>
    <div class="item-text"><strong>Putent voluptaria</strong>sadipscing id sed. Pau lo utinam repudi<div class="item-links"><a>Add</a><a>Participate</a></div></div></div>
  <div class="divider"></div>
  <div class="biz-item"><div class="thumb" role="img" aria-label="Social network illustration" style="background:linear-gradient(135deg,#1f5a6a,#5ab0c0)"></div>
    <div class="item-text"><strong>Putent voluptaria</strong>sadipscing id sed. Pau lo utinam repudi<div class="item-links"><a>Add</a><a>Participate</a></div></div></div>
  <div class="divider"></div>
  <div class="biz-item"><div class="thumb" role="img" aria-label="Globe with social media icons" style="background:linear-gradient(135deg,#8fb3d8,#3c6a9a)"></div>
    <div class="item-text"><strong>Putent voluptaria</strong>sadipscing id sed. Pau lo utinam repudi<div class="item-links"><a>Add</a><a>Participate</a></div></div></div>
  <div class="divider"></div>
  <a class="load-more" style="margin-top:16px">Load More</a>

  <div class="band events-band">Our Events</div>
  <div class="event-item"><div class="thumb" role="img" aria-label="Event image: social icons" style="background:linear-gradient(135deg,#1f5a6a,#6ab5c2)"></div>
    <div><strong>PUTENT VOLUPT</strong><em>19 , November 2015</em><div class="item-links"><a>Add</a><a>Subscribe</a></div></div></div>
  <div class="divider"></div>
  <div class="event-item"><div class="thumb" role="img" aria-label="Event image: tablet with icons" style="background:linear-gradient(135deg,#1d3a66,#6fa0d8)"></div>
    <div><strong>PUTENT VOLUPT</strong><em>19 , November 2015</em><div class="item-links"><a>Add</a><a>Subscribe</a></div></div></div>
  <div class="divider"></div>
  <div class="event-item"><div class="thumb" role="img" aria-label="Event image: table with speech bubbles" style="background:linear-gradient(135deg,#b57b45,#d9a46a)"></div>
    <div><strong>PUTENT VOLUPT</strong><em>19 , November 2015</em><div class="item-links"><a>Add</a><a>Subscribe</a></div></div></div>
  <div class="divider"></div>
  <div class="event-item"><div class="thumb" role="img" aria-label="Event image: hands raised" style="background:linear-gradient(135deg,#e9eef4,#c9a48c)"></div>
    <div><strong>PUTENT VOLUPT</strong><em>19 , November 2015</em><div class="item-links"><a>Add</a><a>Subscribe</a></div></div></div>
  <a class="load-more" style="margin-top:26px">Load More</a>
</aside>

<section class="wall-head">
  <h2>Eu duo soleat dissentias <span><svg width="14" height="13" viewBox="0 0 16 14"><path d="M1 6h3v8H1zM5 6l4-6c2 0 2 2 1 4h5l-1 10H5z" fill="#8a9099"/></svg>Like</span></h2>
  <div class="status-box">something about us</div>
  <p>Eu duo soleat dissentias + others</p>
</section>

<article class="panel post" style="top:786px">
  <div class="share"><svg width="11" height="11" viewBox="0 0 12 12"><circle cx="9" cy="2.5" r="2" fill="#444"/><circle cx="2.5" cy="6" r="2" fill="#444"/><circle cx="9" cy="9.5" r="2" fill="#444"/><path d="M9 2.5L2.5 6 9 9.5" stroke="#444" fill="none"/></svg>share</div>
  <div class="avatar" role="img" aria-label="Author photo"></div>
  <div class="meta"><h3>Putent voluptaria sadipscing id sed</h3><div class="src">www.vidstream.net</div>
    <div class="date"><svg width="13" height="12" viewBox="0 0 13 12"><rect x="1" y="1" width="11" height="10" fill="none" stroke="#1f3a5f" stroke-width="1.6"/></svg>19 November , 2015</div></div>
  <p class="body">Maiorum corrumpit intellegam vix ex. Te alterum menandri sed, nam ullum saepe primis te, has dico quodsi nominati te. Duo legere tempor ne. Mel an paulo qualisque assentior</p>
  <div class="video" role="img" aria-label="Video still: team around a table with social icons" style="background:linear-gradient(135deg,#9a6a3c,#c89460 50%,#7f5530)">
    <svg width="46" height="46" viewBox="0 0 46 46"><circle cx="23" cy="23" r="22" fill="rgba(255,255,255,.35)"/><path d="M17 13l16 10-16 10z" fill="#fff"/></svg></div>
  <div class="actions"><span>↶ Replay</span><span>⇄ Dislike</span><span>♥ Likes</span><span>▭ Comments</span></div>
</article>

<article class="panel post" style="top:1202px">
  <div class="share"><svg width="11" height="11" viewBox="0 0 12 12"><circle cx="9" cy="2.5" r="2" fill="#444"/><circle cx="2.5" cy="6" r="2" fill="#444"/><circle cx="9" cy="9.5" r="2" fill="#444"/><path d="M9 2.5L2.5 6 9 9.5" stroke="#444" fill="none"/></svg>share</div>
  <div class="avatar" role="img" aria-label="Author photo"></div>
  <div class="meta"><h3>Integre minimum forensibus in vis</h3><div class="src">www.vidstream.net</div>
    <div class="date"><svg width="13" height="12" viewBox="0 0 13 12"><rect x="1" y="1" width="11" height="10" fill="none" stroke="#1f3a5f" stroke-width="1.6"/></svg>19 November , 2015</div></div>
  <p class="body">Maiorum corrumpit intellegam vix ex. Te alterum menandri sed, nam ullum saepe primis te, has dico quodsi nominati te. Duo legere tempor ne. Mel an paulo qualisque assentior</p>
  <div class="video" role="img" aria-label="Video still: global network of devices" style="background:linear-gradient(135deg,#0f1e33,#1f5a7a 50%,#0c1a2c)">
    <svg width="46" height="46" viewBox="0 0 46 46"><circle cx="23" cy="23" r="22" fill="rgba(255,255,255,.35)"/><path d="M17 13l16 10-16 10z" fill="#fff"/></svg></div>
  <div class="actions"><span>↶ Replay</span><span>⇄ Dislike</span><span>♥ Likes</span><span>▭ Comments</span></div>
</article>

<article class="panel post" style="top:1617px;height:390px">
  <div class="share"><svg width="11" height="11" viewBox="0 0 12 12"><circle cx="9" cy="2.5" r="2" fill="#444"/><circle cx="2.5" cy="6" r="2" fill="#444"/><circle cx="9" cy="9.5" r="2" fill="#444"/><path d="M9 2.5L2.5 6 9 9.5" stroke="#444" fill="none"/></svg>share</div>
  <div class="avatar" role="img" aria-label="Author photo"></div>
  <div class="meta"><h3>Eam no commodo suscipiantur</h3><div class="src">www.vidstream.net</div>
    <div class="date"><svg width="13" height="12" viewBox="0 0 13 12"><rect x="1" y="1" width="11" height="10" fill="none" stroke="#1f3a5f" stroke-width="1.6"/></svg>19 November , 2015</div></div>
  <p class="body">Maiorum corrumpit intellegam vix ex. Te alterum menandri sed, nam ullum saepe primis te, has dico quodsi nominati te. Duo legere tempor ne. Mel an paulo qualisque assentior</p>
  <div class="video" role="img" aria-label="Video still: business team meeting from above" style="background:linear-gradient(135deg,#5a6a7a,#9fb0c0 50%,#4a5866)">
    <svg width="46" height="46" viewBox="0 0 46 46"><circle cx="23" cy="23" r="22" fill="rgba(255,255,255,.35)"/><path d="M17 13l16 10-16 10z" fill="#fff"/></svg></div>
  <div class="actions"><span>↶ Replay</span><span>⇄ Dislike</span><span>♥ Likes</span><span>▭ Comments</span></div>
</article>

<aside class="panel right-col">
  <div class="band">Social Feed</div>
  <div class="feed-item" style="color:var(--friendnet)"><i style="background:var(--friendnet)"></i>FRIENDNET</div>
  <div class="feed-item" style="color:var(--chirpline)"><i style="background:var(--chirpline)"></i>CHIRPLINE</div>
  <div class="feed-item" style="color:var(--rss)"><i style="background:var(--rss)"></i>RSS</div>
  <div class="feed-item" style="color:var(--circle)"><i style="background:var(--circle)"></i>CIRCLEPOST</div>

  <div class="band friends-band">Friends<b>15</b></div>
  <ul class="friend-list">
    <li class="on">Sed eu nullam</li><li>Mea fabulas elaborare</li><li class="on">Te alterum menandri</li>
    <li>sententiae</li><li>vim ut movet</li><li>Suscipiantur Sed eu</li><li class="on">sententiae dissentias</li>
    <li class="on">Sed eu nullam</li><li>erat dolore principe</li><li class="on">Sed eu nullam</li><li>utinam repudiare</li>
  </ul>

  <div class="band pc-band">Post and Comment</div>
  <div class="pc-item"><div class="thumb" role="img" aria-label="Group photo" style="background:linear-gradient(135deg,#6a5a4a,#b8a08a)"></div>
    <div><strong>Te alterum menandri</strong><span>Integre minimum forensibus</span><small>Like • comment<em>3 hours ago</em></small></div></div>
  <div class="pc-item"><div class="thumb" role="img" aria-label="Writing at a desk" style="background:linear-gradient(135deg,#2a2f48,#b89a84)"></div>
    <div><strong>Quod justo nec</strong><span>Integre minimum forensibus</span><small>Like • comment<em>3 hours ago</em></small></div></div>
  <div class="pc-item"><div class="thumb" role="img" aria-label="Digital network visual" style="background:linear-gradient(135deg,#0c3a4a,#3ab0c8)"></div>
    <div><strong>Nam ullum saepe</strong><span>Integre minimum forensibus</span><small>Like • comment<em>3 hours ago</em></small></div></div>
  <div class="pc-item"><div class="thumb" role="img" aria-label="Business handshake" style="background:linear-gradient(135deg,#3a4050,#c0a890)"></div>
    <div><strong>Commodo suscipiantur</strong><span>Integre minimum forensibus</span><small>Like • comment<em>3 hours ago</em></small></div></div>
  <a class="load-more" style="margin-top:22px">Load More</a>
</aside>

<div class="loader">
  <svg width="36" height="36" viewBox="0 0 36 36"><g fill="#222"><circle cx="18" cy="4" r="3"/><circle cx="28" cy="8" r="2.8"/><circle cx="32" cy="18" r="2.6"/><circle cx="28" cy="28" r="2.4"/><circle cx="18" cy="32" r="2.2"/><circle cx="8" cy="28" r="2"/><circle cx="4" cy="18" r="1.8"/><circle cx="8" cy="8" r="1.6"/></g></svg>
  <div>LOADING...</div>
</div>

<footer class="site-footer">All Rights Reserved . Copyrights2015@companyname.com</footer>

</body>
</html>
```